Business Card Design for Occupational Medicine Start Up Company

We need to design a professional business card. We are a healthcare company providing occupational medicine services to blue collar industries. We are professional, efficient and high quality service providers.

Target Market(s)

Blue Collar Industry: Shipbuilding, Ports, Trucking Companies; The Executives and Safety Officers for these companies

Industry/Entity Type

Healthcare

Contact Information for Business Card

Logo, Name, Title, Email, Phone

Other font styles liked:
• Please match our Brand Guide

Requirements
Must have
• Our Company Colors and Logo

```html
<!DOCTYPE html>
<html lang="en">
<head>
<meta charset="utf-8">
<title>ShiftWell Clinics – Business Card</title>
<link rel="stylesheet" href="https://fonts.googleapis.com/css2?family=Montserrat:wght@400;500;700&display=swap">
<style>
  :root {
    --navy: #2b3580;
    --white: #ffffff;
    --ink-grey: #6d6e71;
    --backdrop: #e3e3e3;
  }
  * { box-sizing: border-box; margin: 0; padding: 0; }
  html, body {
    width: 1200px;
    height: 900px;
    overflow: hidden;
    background: var(--backdrop);
    font-family: "Montserrat", Arial, sans-serif;
  }
  .card {
    position: absolute;
    left: 328px;
    width: 445px;
    height: 253px;
    overflow: hidden;
  }
  .card--front { top: 166px; background: var(--white); }
  .card--back  { top: 467px; background: var(--navy); }

  .brand-panel {
    position: absolute;
    left: 0; top: 0;
    width: 194px; height: 100%;
    background: var(--navy);
  }
  .brand {
    position: absolute;
    display: flex;
    flex-direction: column;
    align-items: center;
    color: var(--white);
    font-weight: 700;
    text-align: center;
  }
  .brand__dot {
    background: var(--white);
    border-radius: 50%;
  }
  .brand--small {
    left: 0; top: 86px; width: 194px;
    font-size: 15px;
    letter-spacing: 0.3px;
    line-height: 1.15;
  }
  .brand--small .brand__dot { width: 30px; height: 30px; margin-bottom: 12px; }
  .brand--small .brand__sub { font-size: 10px; letter-spacing: 3.5px; }

  .brand--large {
    left: 0; top: 0; width: 100%; height: 100%;
    flex-direction: row;
    justify-content: center;
    gap: 20px;
    font-size: 28px;
    letter-spacing: 0.5px;
    line-height: 1.05;
  }
  .brand--large .brand__dot { width: 64px; height: 64px; flex: none; }
  .brand--large .brand__text { display: flex; flex-direction: column; align-items: center; }
  .brand--large .brand__sub { font-size: 16px; letter-spacing: 6px; }

  .contact {
    position: absolute;
    left: 207px;
    top: 83px;
    color: var(--ink-grey);
  }
  .contact__name {
    font-size: 16.5px;
    font-weight: 400;
    color: var(--navy);
    letter-spacing: 0.3px;
    line-height: 1.1;
  }
  .contact__name strong { font-weight: 700; }
  .contact__title {
    font-size: 14px;
    letter-spacing: 0.4px;
    margin-top: 2px;
  }
  .contact__line {
    font-size: 12.5px;
    letter-spacing: 0.2px;
    margin-top: 10px;
  }
  .contact__line + .contact__line { margin-top: 8px; }
</style>
</head>
<body>

  <section class="card card--front" aria-label="Business card front">
    <div class="brand-panel">
      <div class="brand brand--small">
        <span class="brand__dot" aria-hidden="true"></span>
        <span class="brand__name">SHIFTWELL</span>
        <span class="brand__sub">CLINICS</span>
      </div>
    </div>
    <div class="contact">
      <p class="contact__name"><strong>DANA</strong> WHITFIELD</p>
      <p class="contact__title">Cardiac Sonographer</p>
      <p class="contact__line">dana.whitfield@shiftwellclinics.com</p>
      <p class="contact__line">555-014-2278</p>
    </div>
  </section>

  <section class="card card--back" aria-label="Business card back">
    <div class="brand brand--large">
      <span class="brand__dot" aria-hidden="true"></span>
      <span class="brand__text">
        <span class="brand__name">SHIFTWELL</span>
        <span class="brand__sub">CLINICS</span>
      </span>
    </div>
  </section>

</body>
</html>
```